Zielgruppe
Ich biete Farbtupferei, Glitzertattoos, Schwangerschaftsbemalung (Belly-Painting), Wunden schminken, Vermietung von einer Popcornmaschine.
Aufgabenstellung
Mein Anliegen betrifft hiermit die Gestaltung einer Website.
In Bezug auf die Website gibt es schon eine gekaufte Domain, welche lautet: frau-pinselmaus.de und kann über VERAX eingerichtet werden.
Auf dieser WEBSITE soll sich folgendes Menü befinden:
- Anfrage stellen/Angebot einholen mit zusätzlicher Frage 'Wie sind Sie auf mich aufmerksam geworden?'
Mit einem Feld für den Namen, E-Mail, Telefonnummer, Gewünschtes Datum.
Sowie die Frage 'Wie sind Sie auf mich aufmerksam geworden?' (zum Ankreuzen) Freunde, Empfehlung, Flyer, soziale medienoder sonstiges.
Gerne auch zum ankreuzen welche Leistung Sie möchten. Farbtupferei, Glitzer Tattoos, Schwangerschaftsbemalung, oder Popcornmaschiene. (So brauchen haben es die Kunden einfacher nur anzukreuzen und ich sehe gleich worum es sich handelt.)
- eine Leistungsübersicht: Farbtupferei, Glitzertattoos, Schwangerschaftsbemalung (Belly-Painting), Wunden schminken, Vermietung von einer Popcornmaschine
- meine Kontaktdaten
- Galerie (es kann eine Auswahl der angehängten Bilder sein)
!!! mein Wunsch wäre, dass sich die Figur von dem Logo in verschiedenen Positionen auf der Website an das Menü angepasst wiederfindet (wenn dies irgendwie machbar ist)
z.B. meine Figur (Logo) stehend am Rand oder liegend.....
- erwünscht ist auch eine Verknüpfung mit einem Findlaeintrag
- Hinweis auf Kontaktor und Lumoravue (bin gerade dabei ein öffentliches Profil dort zu erstellen)
!Wichtig wäre die nötige Einstellung, damit die Website sowohl in der mobilen Version als auch der PC-Version mit ALLEN oben genannten Informationen dargestellt wird!
Dankbar wäre ich noch für die Information, ob für mich laufende Kosten (monatlich oder jährlich) für die Website entstehen?
Mein Logo ist mir sehr wichtig und sollte gut sichtbar und erkennbar sein auch die Schriftart kann auf der Website aufgegriffen werden

```html
<!DOCTYPE html>
<html lang="de">
<head>
<meta charset="utf-8">
<title>Frau Pinselmaus – Kontakt</title>
<link rel="stylesheet" href="https://fonts.googleapis.com/css2?family=Gentium+Book+Plus:wght@400;700&family=Caveat+Brush&display=swap">
<style>
:root{
  --teal:#1a9cb0;
  --field:#a5d9e2;
  --field-low:#b6e1e8;
  --brush:#a9dce4;
  --ink:#3b3631;
  --nav:#6a6055;
  --sky:#e6f4f6;
  --figure:#c7dfe2;
}
*{box-sizing:border-box;margin:0;padding:0}
html,body{width:899px;height:1200px;overflow:hidden}
body{position:relative;background:#fff;font-family:"Gentium Book Plus",serif;color:var(--ink)}
.site-header{position:absolute;left:0;top:0;width:899px;height:190px;background:linear-gradient(#e4f3f5,#e9f5f7 70%,#fff)}
.brand{position:absolute;display:block;text-decoration:none}
.brand-figure{position:absolute;background:var(--figure);border-radius:40% 40% 20% 20%}
.brand-name{position:absolute;left:0;color:var(--teal);font-weight:700;white-space:nowrap}
.brand-tag{position:absolute;left:0;font-size:8px;line-height:10px;letter-spacing:.3px;color:var(--nav);white-space:nowrap}
.header-brand{left:52px;top:26px;width:230px;height:150px}
.header-brand .brand-figure{left:135px;top:0;width:90px;height:146px}
.header-brand .brand-name{top:56px;font-size:26px;line-height:30px}
.header-brand .brand-tag{top:137px}
.main-nav{position:absolute;top:88px;left:0;width:899px;font-weight:700;font-size:18px;color:var(--nav)}
.main-nav a{position:absolute;color:inherit;text-decoration:none}
.brush{position:absolute;left:35px;top:290px;width:443px;height:130px;background:var(--brush);border-radius:40% 10% 45% 8%/30% 60% 30% 60%;transform:rotate(-4deg)}
.lead{position:absolute;left:60px;top:318px;width:320px;text-align:center;font-family:"Caveat Brush",cursive;font-size:33px;line-height:38px;color:var(--ink);font-weight:400}
.contact-list{position:absolute;left:69px;top:0;list-style:none}
.contact-list li{position:absolute;left:0;width:320px;font-size:20px;line-height:26px}
.contact-list svg{position:absolute;left:0}
.contact-list span{position:absolute;left:55px;white-space:nowrap}
.mark{position:absolute;left:0;width:32px;height:32px;background:var(--teal)}
.form-title{position:absolute;left:528px;top:322px;width:282px;text-align:center;font-size:22px;font-weight:400;color:#111}
.field{position:absolute;left:528px;width:304px;height:34px;border-radius:12px;background:var(--field);font-size:11px;letter-spacing:.3px;padding:11px 17px;color:var(--ink)}
.field svg{position:absolute;right:14px;top:7px}
.field-message{left:530px;top:675px;height:88px;background:linear-gradient(var(--field) 80%,var(--field-low) 80%)}
.send{position:absolute;left:595px;top:785px;width:153px;height:28px;border-radius:12px;background:#fff;box-shadow:0 2px 3px rgba(0,0,0,.25);text-align:center;font-size:14px;line-height:28px;color:var(--nav);letter-spacing:.5px}
.site-footer{position:absolute;left:0;top:900px;width:899px;height:300px;background:linear-gradient(#fff,#eaf6f8 70%,#e2f2f5)}
.footer-brand{left:66px;top:22px;width:290px;height:185px}
.footer-brand .brand-figure{left:180px;top:0;width:100px;height:182px}
.footer-brand .brand-name{top:90px;font-size:34px;line-height:38px}
.footer-brand .brand-tag{top:172px;font-size:10px;line-height:12px}
.footer-title{position:absolute;top:55px;font-family:"Caveat Brush",cursive;font-size:26px;font-weight:400;color:var(--ink)}
.footer-text{position:absolute;font-size:18px;line-height:28px;white-space:nowrap}
.footer-social{position:absolute;font-size:14px;line-height:17px}
.footer-social i{position:absolute;left:-36px;top:3px;width:25px;height:25px;background:var(--ink)}
.copyright{position:absolute;left:0;top:262px;width:899px;text-align:center;font-size:16px;color:var(--nav)}
</style>
</head>
<body>
<header class="site-header">
  <a class="brand header-brand" href="#">
    <span class="brand-figure" role="img" aria-label="Logofigur: Mädchen mit Schleife und Pinsel"></span>
    <span class="brand-name">Frau<br>Pinselmaus</span>
    <span class="brand-tag">FARBTUPFEREI &amp; GLITZER TATTOOS</span>
  </a>
  <nav class="main-nav">
    <a href="#" style="left:404px">HOME</a>
    <a href="#" style="left:525px">LEISTUNGEN</a>
    <a href="#" style="left:682px">KONTAKT</a>
  </nav>
</header>

<main>
  <div class="brush" role="img" aria-label="Hellblauer Pinselstrich als Hintergrund der Überschrift"></div>
  <h2 class="lead">Wie sind Sie auf mich aufmerksam geworden?</h2>

  <ul class="contact-list">
    <li style="top:440px">
      <svg width="30" height="26" viewBox="0 0 24 24"><path fill="#1a9cb0" d="M6.6 10.8a15 15 0 0 0 6.6 6.6l2.2-2.2a1 1 0 0 1 1-.25 11.4 11.4 0 0 0 3.6.6 1 1 0 0 1 1 1V20a1 1 0 0 1-1 1A17 17 0 0 1 3 4a1 1 0 0 1 1-1h3.5a1 1 0 0 1 1 1c0 1.25.2 2.45.6 3.6a1 1 0 0 1-.25 1z"/></svg>
      <span style="left:60px">+ 0040-000 00 88</span>
    </li>
    <li style="top:497px">
      <svg width="32" height="26" viewBox="0 0 32 26"><rect x="2" y="2" width="28" height="22" rx="2" fill="none" stroke="#1a9cb0" stroke-width="3"/><path d="M3 4l13 10 13-10" fill="none" stroke="#1a9cb0" stroke-width="3"/></svg>
      <span>lotte@postfach.de</span>
    </li>
    <li style="top:552px">
      <i class="mark" style="top:8px;border-radius:50%"></i>
      <span>Farbtupferei<br>Lotte Pinselmaus</span>
    </li>
    <li style="top:625px">
      <i class="mark" style="top:1px;border-radius:5px"></i>
      <span>Lotte Pinselmaus</span>
    </li>
  </ul>

  <h2 class="form-title">Anfrage stelle</h2>
  <div class="field" style="top:391px">Name*</div>
  <div class="field" style="top:447px">Email*</div>
  <div class="field" style="top:503px">Telefonnummer</div>
  <div class="field" style="top:560px">Wählen Sie ein Service
    <svg width="20" height="20" viewBox="0 0 20 20"><path d="M3 7l7 6 7-6" fill="none" stroke="#3b3631" stroke-width="2"/></svg>
  </div>
  <div class="field" style="top:616px">Wählen Sie ein Datum
    <svg width="24" height="22" viewBox="0 0 24 24"><rect x="3" y="5" width="18" height="16" rx="2" fill="none" stroke="#3b3631" stroke-width="2"/><path d="M3 10h18M8 2v5M16 2v5" stroke="#3b3631" stroke-width="2"/></svg>
  </div>
  <div class="field field-message">Nachricht</div>
  <div class="send">Senden!</div>
</main>

<footer class="site-footer">
  <a class="brand footer-brand" href="#">
    <span class="brand-figure" role="img" aria-label="Logofigur: Mädchen mit Schleife und Pinsel"></span>
    <span class="brand-name">Frau<br>Pinselmaus</span>
    <span class="brand-tag">FARBTUPFEREI &amp; GLITZER TATTOOS</span>
  </a>
  <h3 class="footer-title" style="left:410px">Kontaktieren Sie uns</h3>
  <h3 class="footer-title" style="left:713px">Information</h3>
  <p class="footer-text" style="left:411px;top:126px">Tel.:&nbsp;&nbsp;&nbsp;&nbsp;&nbsp;+ 0040-000 00 88<br>E-Mail:&nbsp; lotte@postfach.de</p>
  <p class="footer-text" style="left:713px;top:126px">Impressum<br>Datenschutz</p>
  <p class="footer-social" style="left:440px;top:195px"><i style="border-radius:50%"></i>Farbtupferei<br>Lotte Pinselmaus</p>
  <p class="footer-social" style="left:616px;top:194px"><i style="border-radius:5px"></i>Lotte<br>Pinselmaus</p>
  <p class="copyright">Copyright © 2023&nbsp; Farbtupferei Lotte Pinselmaus</p>
</footer>
</body>
</html>
```